Harborline Renewal Business Card Design

Professional and clean design. The design colors should flow with the logo. Two-sided card with the website on the back which is:

www.HarborlineRenewal.example.

"Specializing in Water Damage Restoration"

On the front I need the name, email, phone, and logo.

Name: Darnell Quisby
Email: Darnell@HarborlineRenewal.example
Phone: 555-318-2046 for now

I only have the Preview and Thumbnail right now but should have the source files uploaded within a day or two.

Target Market(s)

Flood victims, home owners with water damage from busted pipes etc...

Industry/Entity Type

Business

Contact Information for Business Card

Name: Darnell Quisby

Font styles to use
Serif
Sans Serif

Requirements
Must have
• Business Card Details Info

```html
<!DOCTYPE html>
<html lang="en">
<head>
<meta charset="utf-8">
<title>Harborline Renewal Business Card</title>
<link rel="stylesheet" href="https://fonts.googleapis.com/css2?family=Cinzel:wght@500&family=Lato:wght@400;700&display=swap">
<style>
  :root {
    --page-bg: #e9ecef;
    --card-white: #ffffff;
    --brand-blue: #2496d6;
    --brand-light: #55c0ef;
    --back-top: #4fbfec;
    --back-bottom: #2f9ed9;
    --text-white: #ffffff;
  }
  * { margin: 0; padding: 0; box-sizing: border-box; }
  html, body { width: 1200px; height: 900px; overflow: hidden; }
  body { background: var(--page-bg); position: relative; font-family: "Lato", Arial, sans-serif; }

  .card { position: absolute; overflow: hidden; box-shadow: 0 4px 14px rgba(0,0,0,0.15); }

  .card-front { left: 78px; top: 34px; width: 588px; height: 364px; background: var(--card-white); }
  .front-bands { position: absolute; inset: 0; }
  .brand-front { position: absolute; left: 90px; top: 48px; display: flex; align-items: center; gap: 18px; }
  .brand-dot { width: 74px; height: 74px; border-radius: 50%; background: var(--brand-blue); }
  .brand-name { font-family: "Cinzel", Georgia, serif; font-weight: 500; color: var(--brand-blue); line-height: 1; text-align: center; }
  .brand-front .brand-main { font-size: 36px; letter-spacing: 1px; display: block; }
  .brand-front .brand-sub { font-size: 19px; letter-spacing: 4px; display: block; margin-top: 6px; }

  .contact { position: absolute; left: 0; right: 0; top: 232px; text-align: center; color: var(--text-white); }
  .contact-name { font-weight: 700; font-size: 21px; margin-bottom: 26px; }
  .contact-line { font-size: 15px; line-height: 24px; display: flex; justify-content: center; align-items: center; gap: 6px; }
  .contact-line svg { width: 12px; height: 12px; fill: var(--text-white); }

  .card-back { left: 388px; top: 506px; width: 566px; height: 350px; background: linear-gradient(180deg, var(--back-top), var(--back-bottom)); }
  .back-ring { position: absolute; left: 50px; top: 8px; width: 420px; height: 420px; border-radius: 50%; border: 26px solid rgba(255,255,255,0.07); }
  .brand-back { position: absolute; left: 0; right: 0; top: 146px; color: var(--text-white); }
  .brand-back .brand-main { font-size: 46px; letter-spacing: 2px; display: block; color: var(--text-white); }
  .brand-back .brand-sub { font-size: 21px; letter-spacing: 5px; display: block; margin-top: 6px; color: var(--text-white); }
  .back-web { position: absolute; left: 0; right: 0; top: 251px; text-align: center; color: var(--text-white); font-weight: 700; font-size: 15px; }
  .back-tagline { position: absolute; left: 0; right: 0; top: 292px; text-align: center; color: var(--text-white); font-weight: 700; font-size: 17px; }
</style>
</head>
<body>
  <section class="card card-front">
    <svg class="front-bands" width="588" height="364" viewBox="0 0 588 364">
      <polygon points="0,168 588,168 588,364 0,364" fill="var(--brand-blue)"/>
      <polygon points="0,168 415,168 380,204 0,204" fill="var(--card-white)"/>
      <polygon points="0,178 402,178 384,197 0,197" fill="var(--brand-light)"/>
    </svg>
    <div class="brand-front">
      <div class="brand-dot"></div>
      <div class="brand-name">
        <span class="brand-main">HARBORLINE</span>
        <span class="brand-sub">RENEWAL</span>
      </div>
    </div>
    <div class="contact">
      <p class="contact-name">Darnell Quisby</p>
      <p class="contact-line">
        <svg viewBox="0 0 24 24"><path d="M6.6 10.8a15 15 0 0 0 6.6 6.6l2.2-2.2a1 1 0 0 1 1-.25 11.4 11.4 0 0 0 3.6.6 1 1 0 0 1 1 1V20a1 1 0 0 1-1 1A17 17 0 0 1 3 4a1 1 0 0 1 1-1h3.5a1 1 0 0 1 1 1 11.4 11.4 0 0 0 .6 3.6 1 1 0 0 1-.25 1z"/></svg>
        555-318-2046
      </p>
      <p class="contact-line">
        <svg viewBox="0 0 24 24"><path d="M2 5h20v14H2z M2 5l10 8 10-8" fill="var(--text-white)"/><path d="M2 5l10 8 10-8" fill="none" stroke="var(--brand-blue)" stroke-width="2"/></svg>
        Darnell@HarborlineRenewal.example
      </p>
    </div>
  </section>

  <section class="card card-back">
    <div class="back-ring"></div>
    <div class="brand-back brand-name">
      <span class="brand-main">HARBORLINE</span>
      <span class="brand-sub">RENEWAL</span>
    </div>
    <p class="back-web">www.HarborlineRenewal.example</p>
    <p class="back-tagline">Specializing in Water Damage Restoration</p>
  </section>
</body>
</html>
```